Business Card Re-Design/Update

We'd like to update out business cards. I've included our current "Style guide" which has the colour scheme of the organisation in it. I've also included the branding files with logos etc in them.

I've also included a copy of one of our existing cards so that you can see how ugly/dated they look. I'd like a fresh modern corporate look.

Target Market(s)

These are for our clients, potential clients, industry contacts - like all business cards

Contact Information for Business Card

Name
Position
Company Address - Level 1, 47 Fernby Street, Carlow Qld 4072
Direct Phone
mobile
Email
Website -www.korvalit.com.au
Logo

Colors

Designer to choose colors to be used in the design.

Requirements
Must have
• Main Logo
• Cards will need to be editable to be able to personalize them for each new employee.
Nice to have
• The MapOut, ShipWell, KeepSteady would be okay to have if they can be sensibly and professionally added to the look without detracting from the main imagery.
• Maybe they could go on the back of the card? will leave this to your creative discretion as to whether/where they fit.
Should not have
• Should not have decorative or script fonts

```html
<!DOCTYPE html>
<html lang="en">
<head>
<meta charset="utf-8">
<title>korvalIT business card</title>
<link href="https://fonts.googleapis.com/css2?family=Work+Sans:wght@400;500;600&display=swap" rel="stylesheet">
<style>
  :root {
    --brand-blue: #1e88d2;
    --ink: #333a40;
    --paper: #ffffff;
    --backdrop: #d9d9d9;
    --back-black: #050708;
    --pattern-navy: #0d1a26;
  }
  html, body {
    margin: 0;
    width: 1200px;
    height: 800px;
    overflow: hidden;
    background: var(--backdrop);
    font-family: "Work Sans", Arial, sans-serif;
  }
  .canvas {
    position: relative;
    width: 1200px;
    height: 800px;
  }
  .card {
    position: absolute;
    top: 247px;
    width: 500px;
    height: 306px;
    overflow: hidden;
    box-shadow: 0 6px 18px rgba(0,0,0,0.18);
  }
  .card-front { left: 70px; background: var(--paper); }
  .card-back { left: 630px; background: var(--back-black); }

  .brand {
    position: absolute;
    left: 42px;
    top: 136px;
    display: flex;
    align-items: center;
    gap: 10px;
  }
  .brand-square {
    width: 22px;
    height: 22px;
    background: var(--brand-blue);
  }
  .brand-name {
    font-size: 30px;
    font-weight: 500;
    color: var(--brand-blue);
    letter-spacing: -0.5px;
  }
  .divider {
    position: absolute;
    left: 268px;
    top: 46px;
    width: 2px;
    height: 176px;
    background: var(--brand-blue);
  }
  .details {
    position: absolute;
    left: 284px;
    top: 40px;
    color: var(--ink);
    font-size: 11px;
    line-height: 14px;
  }
  .person-name {
    margin: 0;
    font-size: 20px;
    line-height: 22px;
    font-weight: 500;
    color: var(--brand-blue);
    letter-spacing: 0.3px;
  }
  .person-role { margin: 0 0 12px; }
  .address { margin: 0 0 12px; font-style: normal; }
  .contact-list { list-style: none; margin: 0; padding: 0; }
  .contact-list li { display: flex; align-items: center; gap: 7px; }
  .contact-list svg { width: 8px; height: 8px; fill: var(--brand-blue); flex: none; }
  .web-accent { color: var(--brand-blue); }

  .base-band {
    position: absolute;
    left: 0;
    bottom: 0;
    width: 340px;
    height: 10px;
    background: var(--brand-blue);
    clip-path: polygon(0 0, 100% 0, 97% 100%, 0 100%);
  }
  .base-band-edge {
    position: absolute;
    left: 332px;
    bottom: 0;
    width: 168px;
    height: 3px;
    background: var(--ink);
  }

  .back-pattern {
    position: absolute;
    inset: 0;
    background: linear-gradient(135deg, var(--pattern-navy), var(--back-black));
  }
  .back-mark {
    position: absolute;
    left: 236px;
    top: 140px;
    width: 28px;
    height: 28px;
    background: var(--brand-blue);
  }
</style>
</head>
<body>
<main class="canvas">
  <section class="card card-front" aria-label="Card front">
    <div class="brand">
      <span class="brand-square"></span>
      <span class="brand-name">korvalIT</span>
    </div>
    <div class="divider"></div>
    <div class="details">
      <p class="person-name">MARA HOLLOWAY</p>
      <p class="person-role">Business Development Manager</p>
      <address class="address">Level 1, 47 Fernby Street,<br>Carlow Qld 4072</address>
      <ul class="contact-list">
        <li><svg viewBox="0 0 8 8"><rect x="2" y="0" width="4" height="8" rx="1"/></svg>+61 (0)412 555 018</li>
        <li><svg viewBox="0 0 8 8"><rect x="0" y="2" width="8" height="6" rx="1"/></svg>+61 (0)7 3555 0142</li>
        <li><svg viewBox="0 0 8 8"><path d="M1 0h2l1 2-1 1c1 1 1 1 2 2l1-1 2 1v2C4 8 0 4 1 0z"/></svg>+61 (0)7 3555 0100</li>
        <li><svg viewBox="0 0 8 8"><rect x="1" y="3" width="6" height="5"/><rect x="2" y="0" width="4" height="3"/></svg>+61 (0)7 3555 0199</li>
        <li><svg viewBox="0 0 8 8"><path d="M0 1h8v6H0z M0 1l4 3 4-3" /></svg>mholloway@korvalit.com.au</li>
        <li><svg viewBox="0 0 8 8"><circle cx="4" cy="4" r="4"/></svg>www.<span class="web-accent">korvalit</span>.com.au</li>
      </ul>
    </div>
    <div class="base-band"></div>
    <div class="base-band-edge"></div>
  </section>

  <section class="card card-back" aria-label="Card back">
    <div class="back-pattern" role="img" aria-label="Repeating brand pattern in dark navy on black"></div>
    <div class="back-mark"></div>
  </section>
</main>
</body>
</html>
```